Business Card Design for Marketing Firm

Looking for business card design for higher end marketing firm. Clean but impressionable/trendy. We are a marketing firm that represents manufacturers in the foodservice equipment and supply industry. Our customers are end users such has hotels, restaurants, country clubs, convention centers and casinos as well as distributors of restaurants supplies and equipment, and manufacturers of foodservice equipment and supplies.
Target Market(s)
Hotels, Restaurants, Supply & Equipment Distributors, Foodservice Manufacturers
Industry/Entity Type
Foodservice/Hospitality
Contact Information for Business Card
Name, Title, Contact Number, Email, Website, Social Media, Address
Requirements
Must have
- Clean & Simple but Serious and Impressionable

```html
<!DOCTYPE html>
<html lang="en">
<head>
<meta charset="utf-8">
<title>Northgate Partners – Business Card</title>
<link rel="stylesheet" href="https://fonts.googleapis.com/css2?family=Montserrat:wght@400;500;700&display=swap">
<style>
  :root {
    --navy: #3b3a78;
    --paper: #ffffff;
    --ink: #3c3c4c;
    --ink-soft: #5a5a6e;
    --backdrop: #e7e3db;
  }
  * { box-sizing: border-box; margin: 0; padding: 0; }
  html, body {
    width: 900px; height: 1200px; overflow: hidden;
    background: var(--backdrop);
  }
  .canvas { position: relative; width: 900px; height: 1200px; }

  .card {
    position: absolute; width: 735px; height: 445px;
    border-radius: 26px; overflow: hidden;
    box-shadow: 0 8px 22px rgba(0,0,0,0.22);
  }
  .card-front { left: 82px; top: 135px; background: var(--paper); }
  .card-back { left: 88px; top: 640px; background: var(--navy); }

  .wordmark {
    display: flex; align-items: center; gap: 12px;
    font-family: "Montserrat", sans-serif; font-weight: 500;
    white-space: nowrap;
  }
  .wordmark-dot { border-radius: 50%; flex: none; }

  /* Front */
  .front-brand {
    position: absolute; left: 30px; top: 95px; width: 350px; height: 200px;
    display: flex; align-items: center; justify-content: center;
  }
  .front-brand .wordmark { font-size: 25px; color: var(--navy); }
  .front-brand .wordmark-dot { width: 14px; height: 14px; background: var(--navy); }
  .divider {
    position: absolute; left: 392px; top: 120px; width: 2px; height: 152px;
    background: var(--navy);
  }
  .person {
    position: absolute; left: 418px; top: 120px;
    font-family: "Montserrat", sans-serif;
  }
  .person-name { font-size: 29px; font-weight: 700; color: var(--navy); }
  .person-title { font-size: 17px; color: var(--ink-soft); margin-top: 2px; }
  .contacts { list-style: none; margin-top: 22px; }
  .contacts li {
    display: flex; align-items: center; gap: 10px;
    font-size: 16px; color: var(--ink); line-height: 25px;
  }
  .contacts svg { width: 15px; height: 15px; flex: none; }
  .front-rule {
    position: absolute; left: 0; right: 0; bottom: 72px; height: 2px;
    background: var(--navy);
  }
  .address-band {
    position: absolute; left: 0; right: 0; bottom: 0; height: 64px;
    background: var(--navy);
    display: flex; align-items: center; justify-content: center;
    font-family: "Montserrat", sans-serif; font-size: 16px; color: #fff;
    letter-spacing: 0.3px;
  }

  /* Back */
  .back-brand {
    position: absolute; inset: 0;
    display: flex; align-items: center; justify-content: center;
    padding-top: 30px;
  }
  .back-brand .wordmark { font-size: 44px; color: #fff; gap: 18px; }
  .back-brand .wordmark-dot { width: 22px; height: 22px; background: #fff; }
</style>
</head>
<body>
<div class="canvas">

  <section class="card card-front" aria-label="Business card front">
    <div class="front-brand">
      <div class="wordmark"><span class="wordmark-dot"></span>Northgate Partners</div>
    </div>
    <div class="divider"></div>
    <div class="person">
      <div class="person-name">Daniel Marsh</div>
      <div class="person-title">CEO &amp; Founder</div>
      <ul class="contacts">
        <li>
          <svg viewBox="0 0 16 16" aria-hidden="true"><circle cx="8" cy="8" r="8" fill="#3b3a78"/><path d="M5.2 4.2l1.4 1.4-.8 1.2c.6 1.3 1.5 2.2 2.8 2.8l1.2-.8 1.4 1.4-.9 1.3C7.6 11.3 4.7 8.4 4 5.1z" fill="#fff"/></svg>
          (555) 014-2290
        </li>
        <li>
          <svg viewBox="0 0 16 16" aria-hidden="true"><rect x="1" y="3.5" width="14" height="9" rx="1" fill="#3b3a78"/><path d="M1.5 4l6.5 5 6.5-5" stroke="#fff" stroke-width="1.1" fill="none"/></svg>
          info@northgatepartners.com
        </li>
        <li>
          <svg viewBox="0 0 16 16" aria-hidden="true"><circle cx="8" cy="8" r="7" fill="#3b3a78"/><g stroke="#fff" stroke-width="0.9" fill="none"><ellipse cx="8" cy="8" rx="3" ry="6.5"/><path d="M1.5 8h13M2.5 5h11M2.5 11h11"/></g></svg>
          www.northgatepartners.com
        </li>
      </ul>
    </div>
    <div class="front-rule"></div>
    <div class="address-band">420 Cedar Avenue, Suite 900, Bayview, CA 90210</div>
  </section>

  <section class="card card-back" aria-label="Business card back">
    <div class="back-brand">
      <div class="wordmark"><span class="wordmark-dot"></span>Northgate Partners</div>
    </div>
  </section>

</div>
</body>
</html>
```